Design für einen Jahresplaner gesucht
Zielgruppe
Scannen und Designen Zahntechnischer und Zahnmedizinischer Arbeiten und das Fräsen und 3d Drucken von bereits in CAD konstruierten Objekten. Wir verfügen über die modernsten Zahntechnischen Technologien und bieten diese als Dienstleister für Dentallabore an.
Aufgabenstellung
Wir benotigen ein Jahresplaner für unsere Kunden. Die Beigefügte Vorlage dient regelrecht nur der Grösenvorlage.
Das Design soll Technisch und Innovativ sein. Gleischzeitig aber gradlinig und nicht zu verspielt.
Das Logo kann ruhig stark ins Auge fallen. Die Schriftfarben sollen überwigen dunkelgrau sein. Hervorzuhebende Bereiche wie z. B. Sonntage, Feiertage sollten die Logofaben beinhalten. Bilder können auch verwendet werden aber wir würden uns über ein Schönes Layout ohne Bilder auch freuen.
PS: Unter dem Logo muss in Feiner Schrift stehen
eine Marke der Novarel GmbH

```html
<!DOCTYPE html>
<html lang="de">
<head>
<meta charset="utf-8">
<title>Dentavo Jahresplaner 2019</title>
<link href="https://fonts.googleapis.com/css2?family=Roboto:wght@400;700&family=Ubuntu:wght@400;500&display=swap" rel="stylesheet">
<style>
:root{
  --stage:#e6e6e6;
  --paper:#f1f1f1;
  --ink:#3a3a3a;
  --muted:#666;
  --accent-red:#e2272c;
  --accent-blue:#29a3dc;
  --panel:#48484a;
  --strip:#d4d4d4;
}
*{margin:0;padding:0;box-sizing:border-box}
html,body{width:1200px;height:1200px;overflow:hidden;background:var(--stage)}
.planner{position:absolute;left:20px;top:194px;width:1160px;height:812px;background:var(--paper);overflow:hidden;font-family:"Ubuntu",sans-serif;color:var(--ink)}
.planner-header{position:absolute;left:0;top:0;width:1160px;height:152px;display:block}
.month-band{position:absolute;left:0;top:152px;width:1160px;height:20px;background:var(--accent-blue)}
.months{position:absolute;left:38px;top:152px;display:grid;grid-template-columns:repeat(12,82.4px) 130px}
.month h2{height:20px;line-height:20px;font-size:11.3px;font-weight:500;color:#fff;white-space:nowrap}
.month.next-year{padding-left:15px}
.days{list-style:none;margin-top:11px;padding-left:4px}
.days li{display:flex;align-items:center;height:18.55px;font-size:9.4px;white-space:nowrap}
.days li b{font-weight:400;width:17px}
.days li em{font-style:normal;width:18px}
.days li small{font-size:4.4px;line-height:1.1;white-space:normal;max-width:34px;color:var(--ink)}
.days li.rest{color:var(--accent-red)}
.footnote{position:absolute;top:765px;font-size:4.4px;line-height:1.3;color:var(--ink)}
.bottom-strip{position:absolute;left:0;bottom:0;width:1160px;height:17px;background:var(--strip)}
</style>
</head>
<body>
<main class="planner">
<svg class="planner-header" viewBox="0 0 1332 175" preserveAspectRatio="none" xmlns="http://www.w3.org/2000/svg">
  <defs>
    <linearGradient id="photoTone" x1="0" y1="0" x2="1" y2="0.3">
      <stop offset="0" stop-color="#1f1f1f"/>
      <stop offset="0.35" stop-color="#8d8d8d"/>
      <stop offset="0.7" stop-color="#b5b5b5"/>
      <stop offset="1" stop-color="#2c2c2c"/>
    </linearGradient>
    <linearGradient id="productTone" x1="0" y1="0" x2="1" y2="0">
      <stop offset="0" stop-color="#8a8a8a"/>
      <stop offset="0.5" stop-color="#b99a6e"/>
      <stop offset="1" stop-color="#e6e6e6"/>
    </linearGradient>
  </defs>
  <rect class="header-paper" width="1332" height="175" fill="var(--paper)"/>
  <polygon class="header-photo" role="img" aria-label="Foto einer metallenen Zahnbrücke auf Implantaten" points="640,0 1332,0 1332,175 725,175" fill="url(#photoTone)"/>
  <polygon class="panel-accent" points="326,0 336,0 398,112 697,112 728,175 716,175 689,120 392,120" fill="var(--accent-blue)"/>
  <polygon class="product-panel" points="336,0 640,0 697,112 398,112" fill="var(--panel)"/>
  <rect class="product-shots" role="img" aria-label="Fünf Dentalprodukte: Abutments und Kronen" x="395" y="28" width="230" height="68" rx="6" fill="url(#productTone)" opacity="0.55"/>
  <polygon class="year-tag" points="1175,104 1332,104 1332,160 1140,160" fill="var(--panel)"/>
  <text x="1236" y="147" text-anchor="middle" font-family="Roboto, sans-serif" font-weight="700" font-size="40" fill="#fff">2019</text>

  <circle class="brand-dot" cx="55" cy="74" r="22" fill="var(--accent-blue)"/>
  <text class="brand-name" x="88" y="90" font-family="Ubuntu, sans-serif" font-weight="500" font-size="38" fill="#555">Dentavo</text>
  <text class="brand-owner" x="90" y="108" font-family="Ubuntu, sans-serif" font-size="12.5" letter-spacing="3" fill="var(--muted)">Novarel GmbH</text>

  <g class="contact-pills" font-family="Roboto, sans-serif" font-size="18" fill="#fff">
    <polygon points="33,133 230,133 239,162 42,162" fill="var(--panel)"/>
    <polygon points="258,133 455,133 464,162 267,162" fill="var(--panel)"/>
    <polygon points="483,133 688,133 697,162 492,162" fill="var(--panel)"/>
    <g class="icon-globe" fill="none" stroke="#fff" stroke-width="1.4">
      <circle cx="60" cy="148" r="7"/><ellipse cx="60" cy="148" rx="3" ry="7"/><line x1="53" y1="148" x2="67" y2="148"/>
    </g>
    <path class="icon-phone" d="M283 141c2-1 3 0 4 2l1 2c0 1-1 2-2 2 1 2 2 3 4 4 0-1 1-2 2-2l2 1c2 1 3 2 2 4-1 2-3 2-5 1-4-2-7-5-9-9-1-2-1-4 1-5z" fill="#fff"/>
    <g class="icon-fax" fill="#fff">
      <rect x="503" y="141" width="10" height="4"/><rect x="500" y="145" width="16" height="7" rx="1"/><rect x="503" y="150" width="10" height="5" fill="var(--panel)" stroke="#fff" stroke-width="1.2"/>
    </g>
    <text x="76" y="154" textLength="148" lengthAdjust="spacingAndGlyphs">www.dentavo-lab.de</text>
    <text x="314" y="154" textLength="124" lengthAdjust="spacingAndGlyphs">0221-5550140</text>
    <text x="531" y="154" textLength="144" lengthAdjust="spacingAndGlyphs">0221-555014-21</text>
  </g>
</svg>

<div class="month-band"></div>

<section class="months">
  <div class="month">
    <h2>Januar</h2>
    <ol class="days">
      <li class="rest"><b>01</b><em>Di</em><small>Neujahr</small></li>
      <li><b>02</b><em>Mi</em></li><li><b>03</b><em>Do</em></li><li><b>04</b><em>Fr</em></li>
      <li class="rest"><b>05</b><em>Sa</em></li>
      <li class="rest"><b>06</b><em>So</em><small>Heilige Drei Könige*</small></li>
      <li><b>07</b><em>Mo</em></li><li><b>08</b><em>Di</em></li><li><b>09</b><em>Mi</em></li><li><b>10</b><em>Do</em></li><li><b>11</b><em>Fr</em></li>
      <li class="rest"><b>12</b><em>Sa</em></li><li class="rest"><b>13</b><em>So</em></li>
      <li><b>14</b><em>Mo</em></li><li><b>15</b><em>Di</em></li><li><b>16</b><em>Mi</em></li><li><b>17</b><em>Do</em></li><li><b>18</b><em>Fr</em></li>
      <li class="rest"><b>19</b><em>Sa</em></li><li class="rest"><b>20</b><em>So</em></li>
      <li><b>21</b><em>Mo</em></li><li><b>22</b><em>Di</em></li><li><b>23</b><em>Mi</em></li><li><b>24</b><em>Do</em></li><li><b>25</b><em>Fr</em></li>
      <li class="rest"><b>26</b><em>Sa</em></li><li class="rest"><b>27</b><em>So</em></li>
      <li><b>28</b><em>Mo</em></li><li><b>29</b><em>Di</em></li><li><b>30</b><em>Mi</em></li><li><b>31</b><em>Do</em></li>
    </ol>
  </div>
  <div class="month">
    <h2>Februar</h2>
    <ol class="days">
      <li><b>01</b><em>Fr</em></li><li class="rest"><b>02</b><em>Sa</em></li><li class="rest"><b>03</b><em>So</em></li>
      <li><b>04</b><em>Mo</em></li><li><b>05</b><em>Di</em></li><li><b>06</b><em>Mi</em></li><li><b>07</b><em>Do</em></li><li><b>08</b><em>Fr</em></li>
      <li class="rest"><b>09</b><em>Sa</em></li><li class="rest"><b>10</b><em>So</em></li>
      <li><b>11</b><em>Mo</em></li><li><b>12</b><em>Di</em></li><li><b>13</b><em>Mi</em></li><li><b>14</b><em>Do</em><small>Valentinstag</small></li><li><b>15</b><em>Fr</em></li>
      <li class="rest"><b>16</b><em>Sa</em></li><li class="rest"><b>17</b><em>So</em></li>
      <li><b>18</b><em>Mo</em></li><li><b>19</b><em>Di</em></li><li><b>20</b><em>Mi</em></li><li><b>21</b><em>Do</em></li><li><b>22</b><em>Fr</em></li>
      <li class="rest"><b>23</b><em>Sa</em></li><li class="rest"><b>24</b><em>So</em></li>
      <li><b>25</b><em>Mo</em></li><li><b>26</b><em>Di</em></li><li><b>27</b><em>Mi</em></li><li><b>28</b><em>Do</em></li>
    </ol>
  </div>
  <div class="month">
    <h2>März</h2>
    <ol class="days">
      <li><b>01</b><em>Fr</em></li><li class="rest"><b>02</b><em>Sa</em></li><li class="rest"><b>03</b><em>So</em></li>
      <li><b>04</b><em>Mo</em><small>Rosenmontag</small></li><li><b>05</b><em>Di</em><small>Fastnacht</small></li><li><b>06</b><em>Mi</em><small>Ascher­mittwoch</small></li><li><b>07</b><em>Do</em></li><li><b>08</b><em>Fr</em></li>
      <li class="rest"><b>09</b><em>Sa</em></li><li class="rest"><b>10</b><em>So</em></li>
      <li><b>11</b><em>Mo</em></li><li><b>12</b><em>Di</em></li><li><b>13</b><em>Mi</em></li><li><b>14</b><em>Do</em></li><li><b>15</b><em>Fr</em></li>
      <li class="rest"><b>16</b><em>Sa</em></li><li class="rest"><b>17</b><em>So</em></li>
      <li><b>18</b><em>Mo</em></li><li><b>19</b><em>Di</em></li><li><b>20</b><em>Mi</em></li><li><b>21</b><em>Do</em></li><li><b>22</b><em>Fr</em></li>
      <li class="rest"><b>23</b><em>Sa</em></li><li class="rest"><b>24</b><em>So</em></li>
      <li><b>25</b><em>Mo</em></li><li><b>26</b><em>Di</em></li><li><b>27</b><em>Mi</em></li><li><b>28</b><em>Do</em></li><li><b>29</b><em>Fr</em></li>
      <li class="rest"><b>30</b><em>Sa</em></li><li class="rest"><b>31</b><em>So</em><small>Beginn der Sommerzeit</small></li>
    </ol>
  </div>
  <div class="month">
    <h2>April</h2>
    <ol class="days">
      <li><b>01</b><em>Mo</em></li><li><b>02</b><em>Di</em></li><li><b>03</b><em>Mi</em></li><li><b>04</b><em>Do</em></li><li><b>05</b><em>Fr</em></li>
      <li class="rest"><b>06</b><em>Sa</em></li><li class="rest"><b>07</b><em>So</em></li>
      <li><b>08</b><em>Mo</em></li><li><b>09</b><em>Di</em></li><li><b>10</b><em>Mi</em></li><li><b>11</b><em>Do</em></li><li><b>12</b><em>Fr</em></li>
      <li class="rest"><b>13</b><em>Sa</em></li><li class="rest"><b>14</b><em>So</em><small>Palmsonntag</small></li>
      <li><b>15</b><em>Mo</em></li><li><b>16</b><em>Di</em></li><li><b>17</b><em>Mi</em></li><li><b>18</b><em>Do</em><small>Grün­donnerstag</small></li>
      <li class="rest"><b>19</b><em>Fr</em><small>Karfreitag</small></li>
      <li class="rest"><b>20</b><em>Sa</em><small>Karsamstag</small></li><li class="rest"><b>21</b><em>So</em><small>Ostersonntag</small></li>
      <li class="rest"><b>22</b><em>Mo</em><small>Ostermontag</small></li>
      <li><b>23</b><em>Di</em></li><li><b>24</b><em>Mi</em></li><li><b>25</b><em>Do</em></li><li><b>26</b><em>Fr</em></li>
      <li class="rest"><b>27</b><em>Sa</em></li><li class="rest"><b>28</b><em>So</em></li>
      <li><b>29</b><em>Mo</em></li><li><b>30</b><em>Di</em><small>Walpurgis­nacht</small></li>
    </ol>
  </div>
  <div class="month">
    <h2>Mai</h2>
    <ol class="days">
      <li class="rest"><b>01</b><em>Mi</em><small>Tag der Arbeit</small></li>
      <li><b>02</b><em>Do</em></li><li><b>03</b><em>Fr</em></li><li class="rest"><b>04</b><em>Sa</em></li><li class="rest"><b>05</b><em>So</em></li>
      <li><b>06</b><em>Mo</em></li><li><b>07</b><em>Di</em></li><li><b>08</b><em>Mi</em></li><li><b>09</b><em>Do</em></li><li><b>10</b><em>Fr</em></li>
      <li class="rest"><b>11</b><em>Sa</em></li><li class="rest"><b>12</b><em>So</em><small>Muttertag</small></li>
      <li><b>13</b><em>Mo</em></li><li><b>14</b><em>Di</em></li><li><b>15</b><em>Mi</em></li><li><b>16</b><em>Do</em></li><li><b>17</b><em>Fr</em></li>
      <li class="rest"><b>18</b><em>Sa</em></li><li class="rest"><b>19</b><em>So</em></li>
      <li><b>20</b><em>Mo</em></li><li><b>21</b><em>Di</em></li><li><b>22</b><em>Mi</em></li><li><b>23</b><em>Do</em></li><li><b>24</b><em>Fr</em></li>
      <li class="rest"><b>25</b><em>Sa</em></li><li class="rest"><b>26</b><em>So</em></li>
      <li><b>27</b><em>Mo</em></li><li><b>28</b><em>Di</em></li><li><b>29</b><em>Mi</em></li>
      <li class="rest"><b>30</b><em>Do</em><small>Christi Himmelfahrt</small></li><li><b>31</b><em>Fr</em></li>
    </ol>
  </div>
  <div class="month">
    <h2>Juni</h2>
    <ol class="days">
      <li class="rest"><b>01</b><em>Sa</em></li><li class="rest"><b>02</b><em>So</em></li>
      <li><b>03</b><em>Mo</em></li><li><b>04</b><em>Di</em></li><li><b>05</b><em>Mi</em></li><li><b>06</b><em>Do</em></li><li><b>07</b><em>Fr</em></li>
      <li class="rest"><b>08</b><em>Sa</em></li><li class="rest"><b>09</b><em>So</em><small>Pfingst­sonntag</small></li>
      <li class="rest"><b>10</b><em>Mo</em><small>Pfingst­montag</small></li>
      <li><b>11</b><em>Di</em></li><li><b>12</b><em>Mi</em></li><li><b>13</b><em>Do</em></li><li><b>14</b><em>Fr</em></li>
      <li class="rest"><b>15</b><em>Sa</em></li><li class="rest"><b>16</b><em>So</em></li>
      <li><b>17</b><em>Mo</em></li><li><b>18</b><em>Di</em></li><li><b>19</b><em>Mi</em></li>
      <li class="rest"><b>20</b><em>Do</em><small>Fronleichnam*</small></li><li><b>21</b><em>Fr</em></li>
      <li class="rest"><b>22</b><em>Sa</em></li><li class="rest"><b>23</b><em>So</em></li>
      <li><b>24</b><em>Mo</em><small>Johannistag</small></li><li><b>25</b><em>Di</em></li><li><b>26</b><em>Mi</em></li><li><b>27</b><em>Do</em></li><li><b>28</b><em>Fr</em></li>
      <li class="rest"><b>29</b><em>Sa</em><small>Peter und Paul</small></li><li class="rest"><b>30</b><em>So</em></li>
    </ol>
  </div>
  <div class="month">
    <h2>Juli</h2>
    <ol class="days">
      <li><b>01</b><em>Mo</em></li><li><b>02</b><em>Di</em></li><li><b>03</b><em>Mi</em></li><li><b>04</b><em>Do</em></li><li><b>05</b><em>Fr</em></li>
      <li class="rest"><b>06</b><em>Sa</em></li><li class="rest"><b>07</b><em>So</em></li>
      <li><b>08</b><em>Mo</em></li><li><b>09</b><em>Di</em></li><li><b>10</b><em>Mi</em></li><li><b>11</b><em>Do</em></li><li><b>12</b><em>Fr</em></li>
      <li class="rest"><b>13</b><em>Sa</em></li><li class="rest"><b>14</b><em>So</em></li>
      <li><b>15</b><em>Mo</em></li><li><b>16</b><em>Di</em></li><li><b>17</b><em>Mi</em></li><li><b>18</b><em>Do</em></li><li><b>19</b><em>Fr</em></li>
      <li class="rest"><b>20</b><em>Sa</em></li><li class="rest"><b>21</b><em>So</em></li>
      <li><b>22</b><em>Mo</em></li><li><b>23</b><em>Di</em></li><li><b>24</b><em>Mi</em></li><li><b>25</b><em>Do</em></li><li><b>26</b><em>Fr</em></li>
      <li class="rest"><b>27</b><em>Sa</em></li><li class="rest"><b>28</b><em>So</em></li>
      <li><b>29</b><em>Mo</em></li><li><b>30</b><em>Di</em></li><li><b>31</b><em>Mi</em></li>
    </ol>
  </div>
  <div class="month">
    <h2>August</h2>
    <ol class="days">
      <li><b>01</b><em>Do</em></li><li><b>02</b><em>Fr</em></li><li class="rest"><b>03</b><em>Sa</em></li><li class="rest"><b>04</b><em>So</em></li>
      <li><b>05</b><em>Mo</em></li><li><b>06</b><em>Di</em></li><li><b>07</b><em>Mi</em></li><li><b>08</b><em>Do</em></li><li><b>09</b><em>Fr</em></li>
      <li class="rest"><b>10</b><em>Sa</em></li><li class="rest"><b>11</b><em>So</em></li>
      <li><b>12</b><em>Mo</em></li><li><b>13</b><em>Di</em></li><li><b>14</b><em>Mi</em></li>
      <li class="rest"><b>15</b><em>Do</em><small>Mariä Himmelfahrt*</small></li><li><b>16</b><em>Fr</em></li>
      <li class="rest"><b>17</b><em>Sa</em></li><li class="rest"><b>18</b><em>So</em></li>
      <li><b>19</b><em>Mo</em></li><li><b>20</b><em>Di</em></li><li><b>21</b><em>Mi</em></li><li><b>22</b><em>Do</em></li><li><b>23</b><em>Fr</em></li>
      <li class="rest"><b>24</b><em>Sa</em></li><li class="rest"><b>25</b><em>So</em></li>
      <li><b>26</b><em>Mo</em></li><li><b>27</b><em>Di</em></li><li><b>28</b><em>Mi</em></li><li><b>29</b><em>Do</em></li><li><b>30</b><em>Fr</em></li>
      <li class="rest"><b>31</b><em>Sa</em></li>
    </ol>
  </div>
  <div class="month">
    <h2>September</h2>
    <ol class="days">
      <li class="rest"><b>01</b><em>So</em></li>
      <li><b>02</b><em>Mo</em></li><li><b>03</b><em>Di</em></li><li><b>04</b><em>Mi</em></li><li><b>05</b><em>Do</em></li><li><b>06</b><em>Fr</em></li>
      <li class="rest"><b>07</b><em>Sa</em></li><li class="rest"><b>08</b><em>So</em></li>
      <li><b>09</b><em>Mo</em></li><li><b>10</b><em>Di</em></li><li><b>11</b><em>Mi</em></li><li><b>12</b><em>Do</em></li><li><b>13</b><em>Fr</em></li>
      <li class="rest"><b>14</b><em>Sa</em></li><li class="rest"><b>15</b><em>So</em></li>
      <li><b>16</b><em>Mo</em></li><li><b>17</b><em>Di</em></li><li><b>18</b><em>Mi</em></li><li><b>19</b><em>Do</em></li><li><b>20</b><em>Fr</em></li>
      <li class="rest"><b>21</b><em>Sa</em></li><li class="rest"><b>22</b><em>So</em></li>
      <li><b>23</b><em>Mo</em></li><li><b>24</b><em>Di</em></li><li><b>25</b><em>Mi</em></li><li><b>26</b><em>Do</em></li><li><b>27</b><em>Fr</em></li>
      <li class="rest"><b>28</b><em>Sa</em></li><li class="rest"><b>29</b><em>So</em></li>
      <li><b>30</b><em>Mo</em></li>
    </ol>
  </div>
  <div class="month">
    <h2>Oktober</h2>
    <ol class="days">
      <li><b>01</b><em>Di</em></li><li><b>02</b><em>Mi</em></li>
      <li class="rest"><b>03</b><em>Do</em><small>Tag der Deutschen Einheit</small></li><li><b>04</b><em>Fr</em></li>
      <li class="rest"><b>05</b><em>Sa</em></li><li class="rest"><b>06</b><em>So</em><small>Erntedankfest</small></li>
      <li><b>07</b><em>Mo</em></li><li><b>08</b><em>Di</em></li><li><b>09</b><em>Mi</em></li><li><b>10</b><em>Do</em></li><li><b>11</b><em>Fr</em></li>
      <li class="rest"><b>12</b><em>Sa</em></li><li class="rest"><b>13</b><em>So</em></li>
      <li><b>14</b><em>Mo</em></li><li><b>15</b><em>Di</em></li><li><b>16</b><em>Mi</em></li><li><b>17</b><em>Do</em></li><li><b>18</b><em>Fr</em></li>
      <li class="rest"><b>19</b><em>Sa</em></li><li class="rest"><b>20</b><em>So</em></li>
      <li><b>21</b><em>Mo</em></li><li><b>22</b><em>Di</em></li><li><b>23</b><em>Mi</em></li><li><b>24</b><em>Do</em></li><li><b>25</b><em>Fr</em></li>
      <li class="rest"><b>26</b><em>Sa</em></li><li class="rest"><b>27</b><em>So</em><small>Ende der Sommerzeit</small></li>
      <li><b>28</b><em>Mo</em></li><li><b>29</b><em>Di</em></li><li><b>30</b><em>Mi</em></li>
      <li class="rest"><b>31</b><em>Do</em><small>Reformations­tag*</small></li>
    </ol>
  </div>
  <div class="month">
    <h2>November</h2>
    <ol class="days">
      <li class="rest"><b>01</b><em>Fr</em><small>Allerheiligen*</small></li>
      <li class="rest"><b>02</b><em>Sa</em><small>Allerseelen</small></li><li class="rest"><b>03</b><em>So</em></li>
      <li><b>04</b><em>Mo</em></li><li><b>05</b><em>Di</em></li><li><b>06</b><em>Mi</em></li><li><b>07</b><em>Do</em></li><li><b>08</b><em>Fr</em></li>
      <li class="rest"><b>09</b><em>Sa</em></li><li class="rest"><b>10</b><em>So</em></li>
      <li><b>11</b><em>Mo</em><small>St. Martin</small></li><li><b>12</b><em>Di</em></li><li><b>13</b><em>Mi</em></li><li><b>14</b><em>Do</em></li><li><b>15</b><em>Fr</em></li>
      <li class="rest"><b>16</b><em>Sa</em></li><li class="rest"><b>17</b><em>So</em><small>Volks­trauertag</small></li>
      <li><b>18</b><em>Mo</em></li><li><b>19</b><em>Di</em></li>
      <li class="rest"><b>20</b><em>Mi</em><small>Buß- und Bettag*</small></li><li><b>21</b><em>Do</em></li><li><b>22</b><em>Fr</em></li>
      <li class="rest"><b>23</b><em>Sa</em></li><li class="rest"><b>24</b><em>So</em><small>Totensonntag</small></li>
      <li><b>25</b><em>Mo</em></li><li><b>26</b><em>Di</em></li><li><b>27</b><em>Mi</em></li><li><b>28</b><em>Do</em></li><li><b>29</b><em>Fr</em></li>
      <li class="rest"><b>30</b><em>Sa</em></li>
    </ol>
  </div>
  <div class="month">
    <h2>Dezember</h2>
    <ol class="days">
      <li class="rest"><b>01</b><em>So</em><small>1. Advent</small></li>
      <li><b>02</b><em>Mo</em></li><li><b>03</b><em>Di</em></li><li><b>04</b><em>Mi</em></li><li><b>05</b><em>Do</em></li><li><b>06</b><em>Fr</em><small>Nikolaus</small></li>
      <li class="rest"><b>07</b><em>Sa</em></li><li class="rest"><b>08</b><em>So</em><small>2. Advent</small></li>
      <li><b>09</b><em>Mo</em></li><li><b>10</b><em>Di</em></li><li><b>11</b><em>Mi</em></li><li><b>12</b><em>Do</em></li><li><b>13</b><em>Fr</em></li>
      <li class="rest"><b>14</b><em>Sa</em></li><li class="rest"><b>15</b><em>So</em><small>3. Advent</small></li>
      <li><b>16</b><em>Mo</em></li><li><b>17</b><em>Di</em></li><li><b>18</b><em>Mi</em></li><li><b>19</b><em>Do</em></li><li><b>20</b><em>Fr</em></li>
      <li class="rest"><b>21</b><em>Sa</em></li><li class="rest"><b>22</b><em>So</em><small>4. Advent</small></li>
      <li><b>23</b><em>Mo</em></li><li><b>24</b><em>Di</em><small>Heiligabend</small></li>
      <li class="rest"><b>25</b><em>Mi</em><small>1. Weihnachts­feiertag</small></li>
      <li class="rest"><b>26</b><em>Do</em><small>2. Weihnachts­feiertag</small></li>
      <li><b>27</b><em>Fr</em></li><li class="rest"><b>28</b><em>Sa</em></li><li class="rest"><b>29</b><em>So</em></li>
      <li><b>30</b><em>Mo</em></li><li><b>31</b><em>Di</em><small>Silvester</small></li>
    </ol>
  </div>
  <div class="month next-year">
    <h2>Januar 2020</h2>
    <ol class="days">
      <li class="rest"><b>01</b><em>Mi</em><small>Neujahr</small></li>
      <li><b>02</b><em>Do</em></li><li><b>03</b><em>Fr</em></li>
      <li class="rest"><b>04</b><em>Sa</em></li><li class="rest"><b>05</b><em>So</em></li>
      <li class="rest"><b>06</b><em>Mo</em><small>Heilige Drei Könige*</small></li>
      <li><b>07</b><em>Di</em></li><li><b>08</b><em>Mi</em></li><li><b>09</b><em>Do</em></li><li><b>10</b><em>Fr</em></li>
      <li class="rest"><b>11</b><em>Sa</em></li><li class="rest"><b>12</b><em>So</em></li>
      <li><b>13</b><em>Mo</em></li><li><b>14</b><em>Di</em></li><li><b>15</b><em>Mi</em></li><li><b>16</b><em>Do</em></li><li><b>17</b><em>Fr</em></li>
      <li class="rest"><b>18</b><em>Sa</em></li><li class="rest"><b>19</b><em>So</em></li>
      <li><b>20</b><em>Mo</em></li><li><b>21</b><em>Di</em></li><li><b>22</b><em>Mi</em></li><li><b>23</b><em>Do</em></li><li><b>24</b><em>Fr</em></li>
      <li class="rest"><b>25</b><em>Sa</em></li><li class="rest"><b>26</b><em>So</em></li>
      <li><b>27</b><em>Mo</em></li><li><b>28</b><em>Di</em></li><li><b>29</b><em>Mi</em></li><li><b>30</b><em>Do</em></li><li><b>31</b><em>Fr</em></li>
    </ol>
  </div>
</section>

<p class="footnote" style="left:38px">*Heilige Drei Könige: BW, BY, ST</p>
<p class="footnote" style="left:450px">*Fronleichnam: BW, BY, HE, NW, RP, SL</p>
<p class="footnote" style="left:614px">*Mariä Himmelfahrt: BY, SL</p>
<p class="footnote" style="left:779px">*Reformationstag:<br>BB, HH, MV, NI, SH, SN, ST, TH</p>
<p class="footnote" style="left:862px">*Allerheiligen: BW, BY, NW, RP, SL<br>*Buß- und Bettag: SN</p>
<p class="footnote" style="left:1041px">*Heilige Drei Könige: BW, BY, ST</p>

<div class="bottom-strip"></div>
</main>
</body>
</html>
```